Modern business card design for professional copywriter

I'd like a business card design that I can use to have my cards printed out by quillprint.com as a squared corners business card (see artwork and design guidelines here: https://help.quillprint.com/hc/en-gb/sections/200570950-QUILL-Product-Templates)

The design should be clean and modern and reflect the colours, tone and branding on my website: https://tessavorrin.com.au

Target Market(s)

Professionals, B2B small business owners

Industry/Entity Type

Business

Contact Information for Business Card

Tessa Vorrin
m: 0468 905 327
e: tessa@tessavorrin.com.au
w: tessavorrin.com.au

Font styles to use
Sans Serif

Requirements
Must have
• Tagline: "Smart copywriting for clever business people"
• Brand colours: fd8000, 009984, 666666 and black
Nice to have

```html
<!DOCTYPE html>
<html lang="en">
<head>
<meta charset="utf-8">
<title>Tessa Vorrin – Business Card</title>
<link rel="stylesheet" href="https://fonts.googleapis.com/css2?family=Montserrat:wght@400;500;700&display=swap">
<style>
  :root {
    --brand-orange: #fd8000;
    --brand-teal: #009984;
    --card-grey: #666666;
    --ink: #000000;
    --page: #ffffff;
    --shadow: rgba(0, 0, 0, 0.35);
  }
  html, body {
    margin: 0;
    padding: 0;
    width: 1200px;
    height: 930px;
    overflow: hidden;
    background: var(--page);
    font-family: "Montserrat", Arial, sans-serif;
  }
  .canvas {
    position: relative;
    width: 1200px;
    height: 930px;
  }
  .card {
    position: absolute;
    left: 267px;
    width: 666px;
    height: 379px;
    background: var(--card-grey);
    border-radius: 16px;
    box-shadow: 8px 9px 14px var(--shadow);
  }
  .card--front { top: 69px; }
  .card--back { top: 488px; }

  .wordmark {
    position: absolute;
    margin: 0;
    font-weight: 500;
    font-size: 32px;
    letter-spacing: -0.5px;
    color: var(--brand-teal);
    white-space: nowrap;
    line-height: 1;
  }
  .card--front .wordmark {
    left: 60px;
    top: 134px;
  }
  .card--back .wordmark {
    left: 0;
    right: 0;
    text-align: center;
    top: 160px;
  }

  .contact-name {
    position: absolute;
    left: 367px;
    top: 134px;
    margin: 0;
    font-weight: 700;
    font-size: 28px;
    color: var(--ink);
    line-height: 1;
  }
  .contact-list {
    position: absolute;
    left: 366px;
    top: 190px;
    margin: 0;
    padding: 0;
    list-style: none;
  }
  .contact-item {
    display: flex;
    align-items: center;
    height: 22.5px;
    font-size: 18px;
    color: var(--ink);
  }
  .contact-icon {
    width: 16px;
    height: 16px;
    margin-right: 10px;
    flex: none;
  }

  .tagline {
    position: absolute;
    left: 0;
    right: 0;
    top: 252px;
    margin: 0;
    text-align: center;
    font-size: 17px;
    color: var(--ink);
  }
</style>
</head>
<body>
<main class="canvas">
  <section class="card card--front" aria-label="Business card front">
    <p class="wordmark">Tessa Vorrin</p>
    <h1 class="contact-name">Tessa Vorrin</h1>
    <ul class="contact-list">
      <li class="contact-item">
        <svg class="contact-icon" viewBox="0 0 16 16" aria-hidden="true">
          <circle cx="8" cy="8" r="8" fill="var(--ink)"/>
          <rect x="5.3" y="3.2" width="5.4" height="9.6" rx="1" fill="none" stroke="var(--card-grey)" stroke-width="1.2"/>
          <rect x="6.4" y="4.4" width="3.2" height="5.6" fill="var(--card-grey)"/>
        </svg>
        0468 905 327
      </li>
      <li class="contact-item">
        <svg class="contact-icon" viewBox="0 0 16 16" aria-hidden="true">
          <circle cx="8" cy="8" r="8" fill="var(--ink)"/>
          <rect x="3.6" y="5" width="8.8" height="6" fill="none" stroke="var(--card-grey)" stroke-width="1.2"/>
          <path d="M3.8 5.3 L8 8.6 L12.2 5.3" fill="none" stroke="var(--card-grey)" stroke-width="1.2"/>
        </svg>
        tessa@tessavorrin.com.au
      </li>
      <li class="contact-item">
        <svg class="contact-icon" viewBox="0 0 16 16" aria-hidden="true">
          <circle cx="8" cy="8" r="8" fill="var(--ink)"/>
          <circle cx="8" cy="8" r="4.8" fill="none" stroke="var(--card-grey)" stroke-width="1"/>
          <ellipse cx="8" cy="8" rx="2" ry="4.8" fill="none" stroke="var(--card-grey)" stroke-width="1"/>
          <path d="M3.2 8 H12.8 M4 5.6 H12 M4 10.4 H12" stroke="var(--card-grey)" stroke-width="0.9"/>
        </svg>
        tessavorrin.com.au
      </li>
    </ul>
  </section>

  <section class="card card--back" aria-label="Business card back">
    <p class="wordmark">Tessa Vorrin</p>
    <p class="tagline">"Smart copywriting for clever business people"</p>
  </section>
</main>
</body>
</html>
```